IT’S NOT A CLEANING, IT’S YOUR LIFE! TOP TEN REASONS WHY THIS IS NOT JUST A “CLEANING”

We made a list for our patients to let them know why our hygiene appointments are different than other cleanings. Since this is a lot of information, we would like it easily readable within 4-5 feet but we do not want the post to be HUGE. Please see below:

IT’S NOT A CLEANING, IT’S YOUR LIFE!
TOP TEN REASONS WHY THIS IS NOT JUST A “CLEANING”

10. We make you look better. Healthy teeth and gums are more attractive. Recent studies
show that the smile is the first thing people notice and that people with better looking teeth
are more confident and successful.

9. We can relieve your headaches. During your hygiene visit we evaluate for serious bite
issues, many of which lead to muscle soreness, headaches, and migraines.

8. We check for oral cancer. Oral cancer kills 1 person per hour 24 hours a day. The death rate for oral cancer is higher than cancers we routinely hear about such as cervical, thyroid and skin cancer.

7. We make you smell better. During your hygiene visit we eliminate many of the germs that live under your gum tissue and cause bad breath.

6. We save you money. By utilizing the latest dental technology (digital x-rays, mouth
cameras, and magnification glasses) we can help with early detection of tooth and gum
problems and save you the cost of gum surgery, root canals, and implants.

5. We clean in places you cannot. We clean under the gum line and between teeth where
most of the germs hide and cause dental disease. 40% of the bacteria in your mouth lives in
between your teeth.

4. We prevent pain. We identify tooth decay that can lead to nerve involvement and pain,
root canal, and tooth loss.

3. We save your teeth. Most tooth loss is from periodontal/gum disease. At each visit we
evaluate the health of your gums and bone with our periodontal screening. Periodontal
disease, like high blood pressure, is symptomless until it is in advanced stages.

2. We protect your loved ones. Studies have proven that the bacteria that cause dental
disease can be transmitted from person to person. Think about that the next time you kiss
someone!

1. We prolong life. Researchers have linked the inflammation and infection found in the
mouth to heart attacks, strokes, and Alzheimer’s. By reducing infection in your mouth we can
greatly improve your overall health!

```html
<!DOCTYPE html>
<html lang="en">
<head>
<meta charset="utf-8">
<title>It's Not Just a Cleaning — Top Ten Reasons</title>
<link href="https://fonts.googleapis.com/css2?family=Abril+Fatface&family=Montserrat:wght@400;500;600&family=Oswald:wght@500;600&family=Roboto+Condensed:wght@300;700&display=swap" rel="stylesheet">
<style>
  :root {
    --navy: #2c2e6c;
    --sky: #68b0e0;
    --cream: #f8efe4;
    --ice: #c8e2f5;
    --ink: #111111;
    --grey: #7a7a7a;
    --bar: #eeeeee;
    --charcoal: #4a4a4a;
    --white: #ffffff;
  }
  * { margin: 0; padding: 0; box-sizing: border-box; }
  html, body { width: 900px; height: 1200px; overflow: hidden; background: var(--white); }
  .poster { position: relative; width: 900px; height: 1200px; }

  .kicker {
    position: absolute; top: 26px; left: 0; width: 900px; text-align: center;
    font-family: "Montserrat", sans-serif; font-weight: 500; font-size: 36px;
    letter-spacing: 4px; color: var(--ink);
  }
  .title {
    position: absolute; top: 62px; left: 0; width: 900px; text-align: center;
    font-family: "Abril Fatface", serif; font-size: 104px; line-height: 1; color: var(--ink);
  }
  .title-rule {
    position: absolute; top: 172px; left: 145px; width: 575px; height: 7px;
    background: var(--ink); border-radius: 4px;
  }
  .subtitle {
    position: absolute; left: 0; width: 900px; text-align: center; color: var(--grey);
    font-family: "Roboto Condensed", sans-serif;
  }
  .subtitle--light { top: 218px; font-weight: 300; font-size: 31px; letter-spacing: 2px; }
  .subtitle--bold { top: 256px; font-weight: 700; font-size: 38px; letter-spacing: 2px; }

  .reason {
    position: absolute; width: 230px; height: 230px; overflow: hidden;
    font-family: "Montserrat", sans-serif;
  }
  .reason--navy { background: var(--navy); color: var(--white); }
  .reason--navy .reason-number { color: var(--ice); }
  .reason--sky { background: var(--sky); color: var(--white); }
  .reason--sky .reason-number { color: var(--white); }
  .reason--sky .reason-heading { color: var(--navy); }
  .reason--cream { background: var(--cream); color: var(--navy); }

  .reason-number {
    position: absolute; top: 8px; left: 0; width: 100%; text-align: center;
    font-family: "Abril Fatface", serif; font-size: 46px; line-height: 1.1;
  }
  .reason-heading {
    position: absolute; top: 62px; left: 8px;
    font-family: "Oswald", sans-serif; font-weight: 600; font-size: 15.5px;
    letter-spacing: -0.3px; text-transform: uppercase; white-space: nowrap;
  }
  .reason-body {
    position: absolute; top: 95px; left: 8px;
    font-size: 11px; line-height: 1.15; letter-spacing: -0.1px; white-space: nowrap;
  }
  .reason-icon { position: absolute; }

  .c1 { left: 80px; } .c2 { left: 335px; } .c3 { left: 590px; }
  .r1 { top: 328px; } .r2 { top: 583px; } .r3 { top: 838px; }

  .highlight {
    position: absolute; top: 1093px; left: 80px; width: 740px; height: 82px;
    background: var(--bar); font-family: "Montserrat", sans-serif;
  }
  .highlight-icon { position: absolute; left: 22px; top: 13px; }
  .highlight-heading {
    position: absolute; left: 96px; top: 16px;
    font-family: "Oswald", sans-serif; font-weight: 600; font-size: 34px;
    color: var(--charcoal); white-space: nowrap; line-height: 1.3; letter-spacing: -0.3px;
  }
  .highlight-number { font-family: "Abril Fatface", serif; font-weight: 400; margin-right: 6px; }
  .highlight-body {
    position: absolute; left: 365px; top: 21px;
    font-size: 10.2px; line-height: 1.25; color: var(--charcoal); white-space: nowrap;
  }
</style>
</head>
<body>
<main class="poster">
  <header>
    <p class="kicker">IT’S NOT JUST A CLEANING.</p>
    <h1 class="title">It’s your life</h1>
    <div class="title-rule"></div>
    <p class="subtitle subtitle--light">TOP TEN REASONS WHY THIS IS</p>
    <p class="subtitle subtitle--bold">MORE THAN ‘JUST A CLEANING’</p>
  </header>

  <section class="reason reason--navy c1 r1">
    <div class="reason-number">10</div>
    <h2 class="reason-heading">We make you look better.</h2>
    <p class="reason-body">Healthy teeth and gums are more<br>attractive. Recent studies show that<br>the smile is the<br>first thing people<br>notice and that<br>people with better<br>looking teeth are<br>more confident<br>and successful.</p>
    <div class="reason-icon" role="img" aria-label="Smiling lips icon" style="left:120px;top:152px;width:88px;height:52px;border-radius:50%;background:var(--ice)"></div>
  </section>

  <section class="reason reason--sky c2 r1">
    <div class="reason-number">9</div>
    <h2 class="reason-heading">We can relieve your headaches.</h2>
    <p class="reason-body">During your<br>hygiene visit<br>we evaluate<br>for serious bite<br>issues, many of<br>which lead to<br>muscle soreness,<br>headaches, and<br>migraines.</p>
    <div class="reason-icon" role="img" aria-label="Dental chair icon" style="left:124px;top:112px;width:84px;height:92px;border-radius:8px;background:rgba(255,255,255,.85)"></div>
  </section>

  <section class="reason reason--cream c3 r1">
    <div class="reason-number">8</div>
    <h2 class="reason-heading">We check for oral cancer.</h2>
    <p class="reason-body">Oral cancer kills 1<br>person per hour 24<br>hours a day. The<br>death rate for oral<br>cancer is higher than<br>cancers we routinely<br>hear about such as<br>cervical, thyroid and<br>skin cancer.</p>
    <div class="reason-icon" role="img" aria-label="Magnifying glass over a tooth icon" style="left:138px;top:120px;width:74px;height:74px;border-radius:50%;background:var(--navy)"></div>
  </section>

  <section class="reason reason--cream c1 r2">
    <div class="reason-number">7</div>
    <h2 class="reason-heading">We make you smell better.</h2>
    <p class="reason-body">During your hygiene visit we eliminate<br>many of the germs that live under your<br>gum tissue and cause bad breath.</p>
    <div class="reason-icon" role="img" aria-label="Germ icon" style="left:80px;top:148px;width:64px;height:64px;border-radius:50%;background:var(--navy)"></div>
  </section>

  <section class="reason reason--navy c2 r2">
    <div class="reason-number">6</div>
    <h2 class="reason-heading">We save you money.</h2>
    <p class="reason-body">By utilizing the latest dental technology<br>(digital x-rays, mouth cameras, and<br>magnification glasses) we can help<br>with early detection<br>of tooth and gum<br>problems and save<br>you the cost of gum<br>surgery, root canals,<br>and implants.</p>
    <div class="reason-icon" role="img" aria-label="Stack of coins icon" style="left:140px;top:148px;width:60px;height:60px;border-radius:50%;background:var(--ice)"></div>
  </section>

  <section class="reason reason--sky c3 r2">
    <div class="reason-number">5</div>
    <h2 class="reason-heading">We clean in places you cannot.</h2>
    <p class="reason-body">We clean under the<br>gum line<br>and between teeth<br>where most of the<br>germs hide and<br>cause dental disease.<br>40% of the bacteria<br>in your mouth lives in<br>between your teeth.</p>
    <div class="reason-icon" role="img" aria-label="Dental mirror and probe icon" style="left:148px;top:122px;width:52px;height:82px;border-radius:8px;background:rgba(255,255,255,.85)"></div>
  </section>

  <section class="reason reason--sky c1 r3">
    <div class="reason-number">4</div>
    <h2 class="reason-heading">We prevent pain.</h2>
    <p class="reason-body">We identify tooth decay that can lead to<br>nerve involvement and pain, root canal,<br>and tooth loss.</p>
    <div class="reason-icon" role="img" aria-label="Decayed tooth icon" style="left:84px;top:148px;width:56px;height:64px;border-radius:40% 40% 30% 30%;background:rgba(255,255,255,.9)"></div>
  </section>

  <section class="reason reason--cream c2 r3">
    <div class="reason-number">3</div>
    <h2 class="reason-heading">We save your teeth.</h2>
    <p class="reason-body">Most tooth loss is from periodontal<br>gum disease. At each visit we evaluate<br>the health of your gums and bone with<br>our periodontal<br>screening. Periodontal<br>disease, like high<br>blood pressure, is<br>symptomless until it is<br>in advanced stages.</p>
    <div class="reason-icon" role="img" aria-label="First aid kit icon" style="left:140px;top:150px;width:74px;height:58px;border-radius:5px;background:var(--navy)"></div>
  </section>

  <section class="reason reason--navy c3 r3">
    <div class="reason-number">2</div>
    <h2 class="reason-heading">We protect your loved ones.</h2>
    <p class="reason-body">Studies have proven<br>that the bacteria<br>that cause dental<br>disease can be<br>transmitted from<br>person to person.<br>Think about that the<br>next time you kiss<br>someone!</p>
    <div class="reason-icon" role="img" aria-label="Parent and child silhouette" style="left:142px;top:114px;width:68px;height:98px;border-radius:8px;background:var(--ice)"></div>
  </section>

  <section class="highlight">
    <svg class="highlight-icon" width="56" height="56" viewBox="0 0 56 56" role="img" aria-label="Heartbeat icon">
      <circle cx="28" cy="28" r="28" fill="var(--charcoal)"/>
      <polyline points="6,30 18,30 23,18 29,40 34,24 38,30 50,30" fill="none" stroke="var(--white)" stroke-width="3.5" stroke-linejoin="round" stroke-linecap="round"/>
    </svg>
    <h2 class="highlight-heading"><span class="highlight-number">1</span>WE PROLONG LIFE.</h2>
    <p class="highlight-body">Researchers have linked the inflammation and infection found in<br>the mouth to heart attacks, strokes, and Alzheimer’s. By reducing<br>infection in your mouth we can greatly improve your overall health!</p>
  </section>
</main>
</body>
</html>
```